TLK Electricial Contracting Services

Hi guys, after a design for my small electrical company, have logo design files to be incorporated into the layout, the basic concept is electrical contracting services for residential, commercial, industrial & data services, image is clean clear and strong,

Card format is to have a nice clean logo on front,with maybe the Residential – commercial – industrial - data, followed with licensed & insured, followed by contact details on backside of the card.

Target Market(s)

Residential, commercial, industrial sectors.

Industry/Entity Type

Electrical

Contact Information for Business Card

TLK logo,
Residential – commercial – industrial - data
REC: 61307
Email: tlk@vornamail.net.au
Phone: 0487 352 019

Requirements
Must have
• Clean & strong design.
Nice to have
• If possible, I would like the logo colours inverted so the text is orange and the background is black on the front of the card, then the backside of the card be the reverse colour
Should not have
• No Sparks, lightning bolts,

```html
<!DOCTYPE html>
<html lang="en">
<head>
<meta charset="utf-8">
<title>TLK Electrical – Business Card</title>
<link href="https://fonts.googleapis.com/css2?family=Mulish:wght@500;600;700;800&display=swap" rel="stylesheet">
<style>
  :root {
    --bg: #9a9a98;
    --orange: #f47f24;
    --black: #0d0d0d;
    --white: #ffffff;
    --rule: #2a2a2a;
  }
  * { margin: 0; padding: 0; box-sizing: border-box; }
  html, body {
    width: 1200px;
    height: 900px;
    overflow: hidden;
    background: var(--bg);
    font-family: "Mulish", "Helvetica Neue", Arial, sans-serif;
  }
  .stage {
    position: relative;
    width: 1200px;
    height: 900px;
  }
  .card {
    position: absolute;
    top: 295px;
    width: 525px;
    height: 300px;
    box-shadow: 0 6px 18px rgba(0,0,0,0.25);
  }
  .card-front {
    left: 50px;
    background: var(--orange);
    display: flex;
    flex-direction: column;
    align-items: center;
    justify-content: center;
    color: var(--black);
  }
  .card-back {
    left: 625px;
    background: var(--black);
    color: var(--white);
  }
  .brand-mark {
    font-weight: 800;
    font-size: 88px;
    line-height: 0.9;
    letter-spacing: 2px;
  }
  .brand-name {
    font-weight: 800;
    font-size: 19px;
    margin-top: 6px;
    letter-spacing: 0.5px;
  }
  .services {
    font-weight: 700;
    font-size: 13px;
    letter-spacing: 0.6px;
    text-transform: uppercase;
    margin-top: 18px;
  }
  .licence-note {
    font-weight: 600;
    font-size: 12px;
    letter-spacing: 0.5px;
    margin-top: 5px;
  }
  .card-back .brand {
    position: absolute;
    top: 42px;
    right: 40px;
    display: flex;
    flex-direction: column;
    align-items: flex-start;
    color: var(--orange);
  }
  .card-back .brand-mark { font-size: 62px; }
  .card-back .brand-name { font-size: 13px; margin-top: 4px; }
  .person {
    position: absolute;
    left: 36px;
    top: 78px;
  }
  .person-name {
    font-weight: 600;
    font-size: 24px;
    color: var(--white);
  }
  .person-title {
    font-weight: 500;
    font-size: 15px;
    color: var(--orange);
    margin-top: 1px;
  }
  .divider {
    position: absolute;
    left: 36px;
    right: 40px;
    top: 140px;
    height: 1px;
    background: var(--rule);
  }
  .contacts {
    position: absolute;
    right: 40px;
    bottom: 28px;
    list-style: none;
    text-align: right;
  }
  .contacts li {
    display: flex;
    align-items: center;
    justify-content: flex-end;
    gap: 8px;
    font-weight: 600;
    font-size: 16px;
    line-height: 24px;
  }
  .contacts svg {
    width: 11px;
    height: 11px;
    fill: none;
    stroke: var(--orange);
    stroke-width: 1.6;
  }
</style>
</head>
<body>
<main class="stage">
  <section class="card card-front" aria-label="Card front">
    <div class="brand-mark">TLK</div>
    <div class="brand-name">Tarek Lowe Electrical</div>
    <div class="services">Residential – Commercial – Industrial – Data</div>
    <div class="licence-note">Licensed &amp; Insured</div>
  </section>

  <section class="card card-back" aria-label="Card back">
    <div class="person">
      <div class="person-name">Daniel Hart</div>
      <div class="person-title">Managing Director</div>
    </div>
    <div class="brand">
      <div class="brand-mark">TLK</div>
      <div class="brand-name">Tarek Lowe Electrical</div>
    </div>
    <div class="divider"></div>
    <ul class="contacts">
      <li>REC: 61307
        <svg viewBox="0 0 12 12" aria-hidden="true"><path d="M2 6.5 L5 9.5 L10 2.5"/></svg>
      </li>
      <li>0487 352 019
        <svg viewBox="0 0 12 12" aria-hidden="true"><rect x="3" y="1" width="6" height="10" rx="1"/></svg>
      </li>
      <li>tlk@vornamail.net.au
        <svg viewBox="0 0 12 12" aria-hidden="true"><rect x="1" y="2.5" width="10" height="7"/><path d="M1 2.5 L6 6.5 L11 2.5"/></svg>
      </li>
      <li>www.tlkelectrical.net.au
        <svg viewBox="0 0 12 12" aria-hidden="true"><path d="M5 7 L7 5 M4.5 5.5 L3 7 A1.4 1.4 0 0 0 5 9 L6.5 7.5 M7.5 6.5 L9 5 A1.4 1.4 0 0 0 7 3 L5.5 4.5"/></svg>
      </li>
    </ul>
  </section>
</main>
</body>
</html>
```